Im open to ideas.. I was thinking on my business cards aswell as my logo. a place for my name. email. phone number and abn..

ive attched a file with my business logo. which i dont love the colours.. i was think a dark background with charcoal letters so something along those colour schumes but im open to ideas..

BRM Constructions

```html
<!DOCTYPE html>
<html lang="en">
<head>
<meta charset="utf-8">
<title>BRM Constructions – Business Cards</title>
<link rel="stylesheet" href="https://fonts.googleapis.com/css2?family=Source+Sans+3:wght@400;600;700&display=swap">
<style>
  :root {
    --canvas: #ece9e6;
    --card-dark: #050505;
    --gold: #f2c200;
    --gold-light: #ffd100;
    --gold-deep: #d2a71c;
    --text-light: #e4e4e4;
    --text-muted: #cfcfcf;
    --white: #ffffff;
  }
  * { box-sizing: border-box; margin: 0; padding: 0; }
  html, body {
    width: 1200px; height: 900px; overflow: hidden;
    background: var(--canvas);
    font-family: "Source Sans 3", "Myriad Pro", Arial, sans-serif;
  }
  .stage { position: relative; width: 1200px; height: 900px; }

  .card { position: absolute; border-radius: 16px; overflow: hidden; }

  /* Front */
  .card-front {
    left: 78px; top: 35px; width: 587px; height: 363px;
    background: var(--card-dark);
  }
  .brand-front {
    position: absolute; left: 300px; top: 138px; width: 287px;
    text-align: center;
    color: var(--text-muted);
    font-weight: 700; font-size: 30px; letter-spacing: 1px;
    text-transform: uppercase;
  }
  .holder { position: absolute; left: 45px; top: 161px; }
  .holder-name { color: var(--gold); font-weight: 600; font-size: 22px; line-height: 1.1; }
  .holder-role { color: var(--text-light); font-size: 16px; margin-top: 4px; }
  .divider {
    position: absolute; left: 0; right: 0; top: 220px; height: 2px;
    background: var(--gold);
  }
  .details { position: absolute; left: 342px; top: 233px; }
  .abn { color: var(--gold); font-weight: 600; font-size: 16px; margin-bottom: 8px; }
  .contact-list { list-style: none; }
  .contact-item {
    display: flex; align-items: center; gap: 8px;
    color: var(--text-light); font-size: 16px; height: 24.5px;
  }
  .contact-item svg { width: 13px; height: 13px; fill: var(--gold); flex: none; }

  /* Back */
  .card-back {
    left: 390px; top: 507px; width: 565px; height: 348px;
    background: linear-gradient(180deg, var(--gold-light) 0%, var(--gold) 45%, var(--gold-deep) 100%);
  }
  .brand-back {
    position: absolute; left: 0; right: 0; top: 148px;
    text-align: center;
    color: var(--white);
    font-weight: 700; font-size: 38px; letter-spacing: 1.5px;
    text-transform: uppercase;
  }
</style>
</head>
<body>
<main class="stage">
  <section class="card card-front" aria-label="Business card front">
    <div class="brand-front">BRM Constructions</div>
    <div class="holder">
      <p class="holder-name">Daniel Hartley</p>
      <p class="holder-role">Managing Director</p>
    </div>
    <div class="divider"></div>
    <div class="details">
      <p class="abn">ABN NO: 12345</p>
      <ul class="contact-list">
        <li class="contact-item">
          <svg viewBox="0 0 24 24" aria-hidden="true"><path d="M6.6 10.8a15.1 15.1 0 0 0 6.6 6.6l2.2-2.2a1 1 0 0 1 1-.25 11.4 11.4 0 0 0 3.6.57 1 1 0 0 1 1 1V20a1 1 0 0 1-1 1A17 17 0 0 1 3 4a1 1 0 0 1 1-1h3.5a1 1 0 0 1 1 1c0 1.25.2 2.45.57 3.57a1 1 0 0 1-.25 1z"/></svg>
          (044)-555-0182
        </li>
        <li class="contact-item">
          <svg viewBox="0 0 24 24" aria-hidden="true"><path d="M2 5h20v14H2z M2 5l10 8 10-8" fill="var(--gold)"/><path d="M3 6l9 7 9-7" fill="none" stroke="#050505" stroke-width="1.6"/></svg>
          info@brmbuild.com
        </li>
        <li class="contact-item">
          <svg viewBox="0 0 24 24" aria-hidden="true"><circle cx="12" cy="12" r="10"/><path d="M2 12h20M12 2c3 3 3 17 0 20M12 2c-3 3-3 17 0 20" fill="none" stroke="#050505" stroke-width="1.4"/></svg>
          www.brmbuild.com
        </li>
      </ul>
    </div>
  </section>

  <section class="card card-back" aria-label="Business card back">
    <div class="brand-back">BRM Constructions</div>
  </section>
</main>
</body>
</html>
```